Stationery Design Project for Nimbora, Chicago

Nimbora, a street parking application which helps car drivers find a street parking spot by offering an ideal path along which to look for parking. This path is calculated by our algorithm based on data (e.g. historical data, baseball games schedule, etc.). Along this path the driver will find a spot and will also save 70% of the search time. Customer we target is reg. between 21 and 45 yo.

We envision something young, fresh, bright and original. Slightly abstract maybe. It should represent the idea and elements of finding street parking in the city, e.g. car(s), parking spot, people, city, etc. (just ideas!).

Logo is attached.

Requirement:
- Business Cards (2 Sided Full Color CMYK)
- Letterhead (1 Sided Full Color CMYK)
- Envelope (1 Sided Full Color CMYK)
- Sticker (1 Sided Full Color CMYK), round with a 2inch diameter.

Reason: We're starting to get more and more designs and need more time to look into all of them. Very exciting!! Thanks to everybody!

Hi all, we're in the process of selecting our favs. Though choices!!! Really good submissions. Will keep you posted and sorry for the delay.

Target Market(s)

Car drivers and owners between 21 and 45

Industry/Entity Type

Parking

Requirements
Must have
• Sticker should be round and include company URL nimbora.com and the new logo which we will attach soon.
Should not have
• Should not be too serious or boring.

```html
<!DOCTYPE html>
<html lang="en">
<head>
<meta charset="utf-8">
<title>Nimbora — Business Card</title>
<link rel="stylesheet" href="https://fonts.googleapis.com/css2?family=Source+Sans+3:wght@400;600;700&display=swap">
<style>
  :root {
    --backdrop: #ece8e2;
    --card: #ffffff;
    --card-edge: #6f6a64;
    --ink: #2e2e30;
    --ink-soft: #444448;
    --brand-blue: #1747c9;
    --brand-glow: #dfe6f4;
    --halo: #eef0f4;
  }
  * { box-sizing: border-box; margin: 0; padding: 0; }
  html, body {
    width: 1200px; height: 1095px; overflow: hidden;
    background: var(--backdrop);
    font-family: "Source Sans 3", Arial, sans-serif;
    color: var(--ink);
  }
  .stage { position: relative; width: 1200px; height: 1095px; }
  .card {
    position: absolute;
    width: 777px; height: 443px;
    background: var(--card);
    border: 1px solid var(--card-edge);
    box-shadow: 0 2px 6px rgba(0,0,0,0.18);
    overflow: hidden;
  }
  .card--front { left: 84px; top: 64px; }
  .card--back  { left: 330px; top: 569px; }

  /* front */
  .brand-dot {
    position: absolute; left: 59px; top: 39px;
    width: 130px; height: 130px; border-radius: 50%;
    background: var(--brand-blue);
    box-shadow: 0 0 0 9px var(--halo), 0 6px 14px rgba(0,0,0,0.15);
  }
  .brand-name {
    position: absolute; left: 212px; top: 48px;
    font-size: 86px; font-weight: 400; line-height: 1;
    color: var(--ink-soft); letter-spacing: 1px;
  }
  .contact-list {
    position: absolute; left: 56px; top: 218px;
    list-style: none; font-size: 19px; line-height: 27.5px; color: var(--ink);
  }
  .contact-list li { display: flex; align-items: center; gap: 10px; }
  .contact-list svg { width: 16px; height: 16px; flex: none; }
  .address {
    position: absolute; left: 56px; top: 362px;
    font-size: 19px; line-height: 25px; color: var(--ink);
  }
  .name-disc {
    position: absolute; left: 500px; top: 167px;
    width: 246px; height: 246px; border-radius: 50%;
    background: var(--brand-glow);
    box-shadow: 0 0 0 10px var(--halo);
  }
  .holder {
    position: absolute; left: 500px; top: 205px; width: 246px;
    text-align: center;
  }
  .holder__name { font-size: 34px; font-weight: 700; line-height: 1.1; color: #111; }
  .holder__title { font-size: 25px; font-weight: 400; line-height: 1.3; color: #111; }

  /* back */
  .back-dot {
    position: absolute; left: 298px; top: 60px;
    width: 180px; height: 180px; border-radius: 50%;
    background: var(--brand-blue);
    box-shadow: 0 0 0 12px var(--halo), 0 10px 22px rgba(0,0,0,0.16);
  }
  .back-name {
    position: absolute; left: 0; top: 280px; width: 100%;
    text-align: center; font-size: 44px; font-weight: 400; color: var(--ink-soft);
  }
  .back-url {
    position: absolute; left: 0; top: 368px; width: 100%;
    text-align: center; font-size: 28px; letter-spacing: 2.5px; color: var(--ink-soft);
  }
</style>
</head>
<body>
<main class="stage">
  <section class="card card--front" aria-label="Business card front">
    <div class="brand-dot"></div>
    <div class="brand-name">Nimbora</div>

    <ul class="contact-list">
      <li>
        <svg viewBox="0 0 16 16" aria-hidden="true"><path d="M4 1.5l2.2 3-1.4 1.6a8 8 0 0 0 5.1 5.1l1.6-1.4 3 2.2-1.3 2.4C7.5 14.5 1.5 8.5 1.6 2.8z" fill="#2e2e30"/></svg>
        <span>+91 12345 67890</span>
      </li>
      <li>
        <svg viewBox="0 0 16 16" aria-hidden="true"><rect x="4.5" y="1" width="7" height="14" rx="1.5" fill="#2e2e30"/><rect x="6" y="3" width="4" height="4" fill="#fff"/></svg>
        <span>+91 12345 67890</span>
      </li>
      <li>
        <svg viewBox="0 0 16 16" aria-hidden="true"><rect x="1.5" y="4" width="13" height="9" rx="1" fill="#2e2e30"/><path d="M2.5 5l5.5 4 5.5-4" stroke="#fff" stroke-width="1.3" fill="none"/></svg>
        <span>info@nimbora.com</span>
      </li>
      <li>
        <svg viewBox="0 0 16 16" aria-hidden="true"><circle cx="8" cy="8" r="6.5" fill="#2e2e30"/><path d="M1.5 8h13M8 1.5c-3 3.5-3 9.5 0 13M8 1.5c3 3.5 3 9.5 0 13" stroke="#fff" stroke-width="0.9" fill="none"/></svg>
        <span>www.nimbora.com</span>
      </li>
    </ul>

    <p class="address">Complex Name, Street Name<br>Area, City Name,000 000</p>

    <div class="name-disc"></div>
    <div class="holder">
      <p class="holder__name">Your Name</p>
      <p class="holder__title">Title</p>
    </div>
  </section>

  <section class="card card--back" aria-label="Business card back">
    <div class="back-dot"></div>
    <p class="back-name">Nimbora</p>
    <p class="back-url">www.nimbora.com</p>
  </section>
</main>
</body>
</html>
```